Korvile

I'd like new business card design options. I'll need to provide updated contact info although after the deign is complete. We are in IT, specifically in the data backup, archiving and disaster recovery verticals.

Industry/Entity Type

Business

```html
<!DOCTYPE html>
<html lang="en">
<head>
<meta charset="utf-8">
<title>Korvile Business Card</title>
<link href="https://fonts.googleapis.com/css2?family=Montserrat:wght@500;700;800&family=Roboto+Condensed:wght@400;700&display=swap" rel="stylesheet">
<style>
  :root {
    --page-bg: #e8e5e0;
    --card-white: #f7f8f9;
    --brand-blue: #1a78c8;
    --brand-blue-deep: #0f5fae;
    --brand-blue-light: #2f8fdc;
    --accent-teal: #2aa6cf;
    --text-white: #ffffff;
    --rule-light: rgba(255,255,255,0.55);
  }
  * { box-sizing: border-box; margin: 0; padding: 0; }
  html, body { width: 1200px; height: 780px; overflow: hidden; }
  body {
    background: var(--page-bg);
    font-family: "Roboto Condensed", "Arial Narrow", sans-serif;
    position: relative;
  }
  .card {
    position: absolute;
    width: 540px;
    height: 309px;
    top: 236px;
    border-radius: 3px;
    overflow: hidden;
    box-shadow: 0 10px 26px rgba(0,0,0,0.18);
  }
  .card--front { left: 45px; background: var(--card-white); }
  .card--back {
    left: 615px;
    background: radial-gradient(ellipse at 45% 40%, var(--brand-blue-light) 0%, var(--brand-blue) 45%, var(--brand-blue-deep) 100%);
  }

  /* Front */
  .front__brand {
    position: absolute; left: 0; top: 0; width: 100%; height: 118px;
    display: flex; align-items: center; padding-left: 52px; gap: 14px;
  }
  .brand-dot {
    width: 34px; height: 34px; border-radius: 50%;
    background: var(--accent-teal);
    flex: none;
  }
  .brand-name {
    font-family: "Montserrat", sans-serif;
    font-weight: 800;
    font-size: 34px;
    letter-spacing: 6px;
    color: var(--brand-blue);
    line-height: 1;
  }
  .brand-tagline {
    font-family: "Montserrat", sans-serif;
    font-weight: 700;
    font-size: 12px;
    letter-spacing: 2.5px;
    color: var(--accent-teal);
    margin-top: 5px;
  }
  .front__info {
    position: absolute; left: 0; top: 118px; width: 100%; height: 138px;
    background: linear-gradient(180deg, var(--brand-blue-light), var(--brand-blue));
    display: flex; align-items: center; color: var(--text-white);
  }
  .person { width: 250px; padding-left: 32px; white-space: nowrap; }
  .person__name {
    font-weight: 700; font-size: 17px; letter-spacing: 0.3px;
  }
  .person__name .caps { text-transform: uppercase; }
  .person__title { font-size: 15px; text-transform: uppercase; margin-top: 2px; }
  .divider { width: 1px; height: 78px; background: var(--rule-light); flex: none; }
  .contact { padding-left: 20px; font-size: 14.5px; line-height: 1.35; white-space: nowrap; }
  .contact__row { display: flex; align-items: center; gap: 6px; }
  .contact__icon { width: 13px; height: 13px; flex: none; }
  .contact__phones { display: flex; gap: 12px; }
  .front__services {
    position: absolute; left: 0; bottom: 0; width: 100%; height: 50px;
    background: var(--accent-teal);
    border-top: 3px solid var(--card-white);
    color: var(--text-white);
    font-size: 14px; text-transform: uppercase;
    display: flex; align-items: center; justify-content: center; gap: 8px;
  }

  /* Back */
  .back__content {
    position: absolute; inset: 0;
    display: flex; flex-direction: column; align-items: center; justify-content: center;
  }
  .back__brand { display: flex; align-items: center; gap: 14px; }
  .back__brand .brand-name { color: var(--text-white); font-size: 36px; }
  .back__brand .brand-tagline { color: var(--text-white); }
  .back__brand .brand-dot { background: var(--text-white); }
  .back__url {
    font-family: "Montserrat", sans-serif; font-weight: 500;
    color: var(--text-white); font-size: 14px; letter-spacing: 2.5px;
    margin-top: 30px;
  }
</style>
</head>
<body>
  <section class="card card--front" aria-label="Business card front">
    <div class="front__brand">
      <span class="brand-dot"></span>
      <div>
        <div class="brand-name">KORVILE</div>
        <div class="brand-tagline">Backup You Can Trust</div>
      </div>
    </div>
    <div class="front__info">
      <div class="person">
        <div class="person__name"><span class="caps">Daniel R. Whitcombe,</span> Ph.D.</div>
        <div class="person__title">President, CTO</div>
      </div>
      <div class="divider"></div>
      <div class="contact">
        <div>240 North Alder Avenue</div>
        <div>Brookfield, Ohio 44403</div>
        <div class="contact__row">
          <svg class="contact__icon" viewBox="0 0 14 14"><circle cx="7" cy="7" r="7" fill="#fff"/><rect x="3" y="4.5" width="8" height="5.5" fill="none" stroke="#1a78c8" stroke-width="1.1"/><path d="M3 4.8 7 7.8 11 4.8" fill="none" stroke="#1a78c8" stroke-width="1.1"/></svg>
          <span>daniel.whitcombe@korvile.com</span>
        </div>
        <div class="contact__phones">
          <span class="contact__row">
            <svg class="contact__icon" viewBox="0 0 14 14"><circle cx="7" cy="7" r="6.3" fill="none" stroke="#fff" stroke-width="1.2"/><path d="M4.6 3.8c.5-.4 1-.3 1.2.1l.6 1.3c.1.3 0 .6-.3.8l-.4.3c.4.9 1.1 1.6 2 2l.3-.4c.2-.3.5-.4.8-.3l1.3.6c.4.2.5.7.1 1.2-.6.7-1.6.9-2.6.3C6.2 8.9 5.1 7.8 4.4 6.4c-.5-1-.4-2 .2-2.6z" fill="#fff"/></svg>
            <span>800.555.0142</span>
          </span>
          <span class="contact__row">
            <svg class="contact__icon" viewBox="0 0 14 14"><circle cx="7" cy="7" r="7" fill="#fff"/><rect x="3.5" y="5.5" width="7" height="4.5" fill="#1a78c8"/><rect x="4.8" y="3.5" width="4.4" height="2.4" fill="none" stroke="#1a78c8" stroke-width="1"/></svg>
            <span>928.555.0187</span>
          </span>
        </div>
      </div>
    </div>
    <div class="front__services">
      <span>Online PC Backup</span><span>&bull;</span>
      <span>Continuous Server Backup</span><span>&bull;</span>
      <span>Data Archiving</span>
    </div>
  </section>

  <section class="card card--back" aria-label="Business card back">
    <div class="back__content">
      <div class="back__brand">
        <span class="brand-dot"></span>
        <div>
          <div class="brand-name">KORVILE</div>
          <div class="brand-tagline">Backup You Can Trust</div>
        </div>
      </div>
      <div class="back__url">www.korvile.com</div>
    </div>
  </section>
</body>
</html>
```